Pebblebrook Plots - Online-only garden installation company

Online-only garden installation company. Our demographic is middle aged / suburban women, and we anticipate Community Feed driving traffic to this website, as well as referrals from garden centers. The website must be very simple in design and function.

All orders will be placed through the website, including size of garden (3 options), location in yard, payment, and scheduling of installation date.

The website should employ a 3 step process:

Step 1: Select garden size. Either an 4' X 4', 8' X 4', or 12' X 4'.

Step 2: Select a location. We would like to use google maps to look up a US address, then "drag and drop" one of the garden sizes from step 1 to the location the customer would like us to install the garden at their home.

Step 3: Pick an installation date and pay. Using an online calendar the customer will pick a date, and then pay for the installation via credit card.

The website will be linked to an email account, PebblebrookPlots@mailvale.com to inform us of orders placed.

Target Market(s)

Our demographic is middle aged / suburban women, and we anticipate Community Feed driving traffic to this website, as well as referrals from garden centers.

Industry/Entity Type

Coding

Number of Pages Required

Requirements
Must have
• Scheduling and payment options.

```html
<!DOCTYPE html>
<html lang="en">
<head>
<meta charset="utf-8">
<title>Pebblebrook Plots – Garden Installation</title>
<link href="https://fonts.googleapis.com/css2?family=Arimo:wght@400;700&family=Bebas+Neue&family=Cinzel:wght@400;700&family=Cormorant+Garamond:wght@600&display=swap" rel="stylesheet">
<style>
:root{
  --green:#3a8a3e;
  --green-dark:#2c6a30;
  --green-deep:#24582a;
  --orange:#e0602a;
  --orange-dark:#c94f1e;
  --cream:#eef3dc;
  --cream-light:#f6f9ea;
  --soil:#2b1e15;
  --soil-light:#3b2a1e;
  --ink:#3a3a3a;
  --white:#ffffff;
}
*{box-sizing:border-box;margin:0;padding:0}
html,body{width:1200px;height:3169px;overflow:hidden;background:var(--cream)}
body{font-family:"Arimo",Arial,sans-serif;color:var(--ink)}
.canvas{position:relative;width:1200px;height:3169px;overflow:hidden;background:radial-gradient(ellipse at 50% 40%,var(--cream-light),var(--cream))}
.abs{position:absolute}
.center{left:0;width:1200px;text-align:center}

/* nav */
.nav{top:0;left:0;width:1200px;height:89px;background:var(--cream-light)}
.nav a{position:absolute;top:19px;height:51px;line-height:51px;font-size:17px;color:#3e3e3e;text-decoration:none;text-transform:uppercase}
.nav .active{left:213px;width:104px;background:var(--orange);color:var(--white);border-radius:26px;text-align:center}
.nav .login{text-transform:none}
.brand-badge{left:505px;top:0;width:190px;height:182px;border-radius:0 0 95px 95px;background:var(--cream-light);z-index:3;text-align:center}
.brand-badge span{display:block;margin-top:98px;font-family:"Cinzel",serif;font-weight:700;font-size:19px;line-height:24px;color:var(--green-dark)}

/* hero */
.hero{top:89px;left:0;width:1200px;height:545px;background:linear-gradient(180deg,#4f6f3a 0%,#5d7c46 35%,#3f5a31 70%,#2f4a2a 100%)}
.hero-title{top:285px;font-family:"Bebas Neue",sans-serif;font-size:104px;line-height:104px;color:var(--white);letter-spacing:1px}
.hero-band{left:211px;top:412px;width:782px;height:63px;background:rgba(58,138,62,.88);color:var(--white);font-size:22px;line-height:63px;text-align:center}
.hero-arrow{top:357px;width:50px;height:50px;border:2px solid var(--white);border-radius:50%}

/* sections */
.welcome{top:634px;left:0;width:1200px;height:359px;background:var(--green)}
.kicker{font-size:21px;color:var(--white);letter-spacing:1px}
.title{font-family:"Cinzel",serif;font-size:42px;line-height:50px}
.body-copy{font-size:14px;line-height:28px}
.btn{display:block;background:var(--orange);color:var(--white);font-family:"Cinzel",serif;font-size:20px;text-align:center;border-radius:30px;text-transform:uppercase}

.order-card{top:1219px;width:332px;height:334px;background:var(--green)}
.order-card .photo{width:332px;height:275px;background:linear-gradient(160deg,#6e7d5a 0%,#4a3a2b 45%,#c89a63 80%,#7a8a5a 100%)}
.order-card .size{height:59px;line-height:59px;text-align:center;color:var(--white);font-family:"Cinzel",serif;font-size:28px}

.location{top:1574px;left:0;width:1200px;height:740px;background:radial-gradient(ellipse at 50% 50%,#3c8440,#2a6a2f 70%,#235a28)}
.map{left:129px;top:1809px;width:368px;height:368px;border-radius:50%;background:radial-gradient(circle at 50% 55%,#e6e4dc,#d6dccd 70%,#c9d7c0);border:6px solid var(--white)}
.calendar{left:433px;top:1811px;width:634px;height:361px;background:rgba(255,255,255,.16)}
.calendar .month{position:absolute;top:22px;left:0;width:634px;text-align:center;font-family:"Cinzel",serif;font-size:20px;color:var(--orange)}
.calendar .cell{position:absolute;width:60px;margin-left:-30px;text-align:center;color:var(--white);font-size:16px}
.calendar .head{font-size:17px;color:#e8f0de}

.about-title{left:80px;top:2375px;font-family:"Cinzel",serif;font-size:42px;color:var(--green-dark)}
.video{left:727px;top:2371px;width:393px;height:272px;background:linear-gradient(135deg,#5d7a3e,#8aa35a 40%,#c7866d 70%,#4c6a35)}
.play{left:925px;top:2483px;width:80px;height:58px;background:var(--orange);border-radius:10px}

.grass{top:2700px;left:0;width:1200px;height:120px;background:linear-gradient(180deg,rgba(106,165,52,0) 0%,#6aa534 35%,#3f7a24 70%,var(--soil) 100%)}
.footer{top:2810px;left:0;width:1200px;height:359px;background:radial-gradient(ellipse at 50% 30%,var(--soil-light),var(--soil))}
.f-head{top:2842px;font-family:"Cormorant Garamond",serif;font-weight:600;font-size:22px;color:var(--green)}
.f-links{left:80px;top:2887px;list-style:none;color:var(--white);font-size:14px;line-height:28px}
.f-links li::before{content:"";display:inline-block;width:8px;height:8px;border-radius:50%;background:var(--white);margin-right:16px;vertical-align:middle}
.f-text{color:var(--white);font-size:14px;line-height:21px}
.feed{left:608px;top:2884px;width:254px;height:195px;background:var(--white);font-size:11px;color:#555}
.field{left:873px;width:249px;height:40px;border:1px solid #bbb;color:var(--white);font-size:14px;line-height:38px;padding-left:10px}
.copyright{top:3128px;font-size:14px;color:var(--white)}
.copyright b{font-weight:400;color:var(--orange)}
</style>
</head>
<body>
<div class="canvas">

  <!-- hero -->
  <div class="abs hero" role="img" aria-label="Photo of a gardener tipping a wheelbarrow of freshly harvested carrots beside flower beds"></div>
  <svg class="abs" style="left:0;top:600px" width="1200" height="40" viewBox="0 0 1200 40" aria-hidden="true">
    <path d="M0 34 L40 30 L70 35 L120 28 L160 33 L210 27 L260 34 L300 29 L350 32 L400 26 L450 33 L500 28 L540 34 L600 27 L650 32 L700 28 L760 35 L800 29 L850 33 L900 27 L950 34 L1000 29 L1050 33 L1100 28 L1150 34 L1200 30 L1200 40 L0 40Z" fill="var(--green)"/>
  </svg>
  <div class="abs center hero-title">FIND THE BEST</div>
  <div class="abs hero-band">WE PROVIDE THE BEST GARDEN INSTALLATION IN YOUR TOWN</div>
  <svg class="abs" style="left:588px;top:505px" width="24" height="26" viewBox="0 0 24 26" aria-hidden="true">
    <path d="M3 3 L12 11 L21 3 M3 13 L12 21 L21 13" stroke="#fff" stroke-width="3" fill="none"/>
  </svg>
  <div class="abs hero-arrow" style="left:13px">
    <svg width="46" height="46" viewBox="0 0 46 46" aria-hidden="true"><path d="M26 14 L17 23 L26 32" stroke="#fff" stroke-width="3" fill="none"/></svg>
  </div>
  <div class="abs hero-arrow" style="left:1135px">
    <svg width="46" height="46" viewBox="0 0 46 46" aria-hidden="true"><path d="M20 14 L29 23 L20 32" stroke="#fff" stroke-width="3" fill="none"/></svg>
  </div>

  <!-- nav -->
  <nav class="abs nav">
    <a class="active" href="#">Home</a>
    <a href="#" style="left:382px">About</a>
    <a href="#" style="left:753px">Order</a>
    <a href="#" style="left:880px">Contact</a>
    <svg class="abs" style="left:1040px;top:30px" width="20" height="24" viewBox="0 0 20 24" aria-hidden="true">
      <path d="M5 11 V7 a5 5 0 0 1 10 0 V11" stroke="var(--green)" stroke-width="3" fill="none"/>
      <rect x="1" y="10" width="18" height="13" rx="2" fill="var(--green)"/>
    </svg>
    <a class="login" href="#" style="left:1074px">Login</a>
  </nav>
  <div class="abs brand-badge"><span>PEBBLEBROOK<br>PLOTS</span></div>

  <!-- welcome -->
  <section class="abs welcome">
    <div class="abs center kicker" style="top:58px">WELCOME TO</div>
    <h1 class="abs center title" style="top:93px;color:var(--white);font-weight:400">PEBBLEBROOK PLOTS</h1>
    <p class="abs body-copy" style="left:148px;top:150px;width:904px;text-align:center;color:#e7f1e2">Lorem Ipsum is simply dummy text of the printing and typesetting industry. Lorem Ipsum has been the industry's standard dummy text ever since the 1500s, when an unknown printer took a galley of type and scrambled it to make a type specimen book. It has survived not only five centuries, but also the leap into electronic typesetting, remaining essentially unchanged.</p>
    <a class="abs btn" href="#" style="left:507px;top:245px;width:186px;height:55px;line-height:55px">Know More</a>
  </section>
  <svg class="abs" style="left:0;top:978px" width="1200" height="30" viewBox="0 0 1200 30" aria-hidden="true">
    <path d="M0 0 L1200 0 L1200 12 L1150 17 L1100 10 L1040 18 L990 11 L930 19 L880 12 L820 17 L760 10 L700 18 L650 12 L590 19 L530 11 L480 17 L420 10 L360 18 L300 12 L240 19 L180 11 L120 18 L60 12 L0 17Z" fill="var(--green)"/>
  </svg>

  <!-- order -->
  <h2 class="abs center title" style="top:1048px;color:var(--green);font-weight:400;font-size:44px">ODER NOW</h2>
  <p class="abs body-copy" style="left:190px;top:1104px;width:820px;text-align:center">Lorem Ipsum is simply dummy text of the printing and typesetting industry. Lorem Ipsum has been the industry's standard dummy text ever since the 1500s, when an unknown printer took a galley of type and scrambled.</p>
  <div class="abs center" style="top:1173px;font-family:'Cinzel',serif;font-size:16px;color:#444">SELECT GARDEN SIZE</div>
  <div class="abs order-card" style="left:78px"><div class="photo" role="img" aria-label="Photo of a 4 by 4 foot cedar raised garden bed filled with soil"></div><div class="size">4' X 4'</div></div>
  <div class="abs order-card" style="left:433px"><div class="photo" role="img" aria-label="Photo of an empty 8 by 4 foot cedar raised bed frame on grass"></div><div class="size">8' X 4'</div></div>
  <div class="abs order-card" style="left:790px"><div class="photo" role="img" aria-label="Photo of an L-shaped 12 by 4 foot cedar raised bed on gravel"></div><div class="size">12' X 4'</div></div>

  <!-- location -->
  <section class="abs location">
    <h2 class="abs center title" style="top:112px;color:var(--white);font-weight:400;font-size:44px">SELECT YOUR LOCATION</h2>
    <div class="abs center" style="top:175px;font-family:'Cormorant Garamond',serif;font-weight:600;font-size:22px;color:var(--white)">Pick date and Install the garden at their home.</div>
  </section>
  <svg class="abs" style="left:0;top:1560px" width="1200" height="30" viewBox="0 0 1200 30" aria-hidden="true">
    <path d="M0 14 L50 9 L110 16 L170 8 L230 15 L290 10 L350 17 L410 9 L470 15 L530 8 L590 16 L650 10 L710 17 L770 9 L830 15 L890 8 L950 16 L1010 10 L1070 17 L1130 9 L1200 15 L1200 30 L0 30Z" fill="#2f7233"/>
  </svg>
  <svg class="abs" style="left:0;top:2300px" width="1200" height="30" viewBox="0 0 1200 30" aria-hidden="true">
    <path d="M0 0 L1200 0 L1200 14 L1140 19 L1080 12 L1020 20 L960 13 L900 18 L840 11 L780 19 L720 13 L660 20 L600 12 L540 18 L480 11 L420 19 L360 13 L300 20 L240 12 L180 18 L120 11 L60 19 L0 13Z" fill="#235a28"/>
  </svg>
  <div class="abs map" role="img" aria-label="Circular street map showing the customer's neighbourhood"></div>
  <div class="abs calendar" aria-label="Installation date calendar">
    <svg class="abs" style="left:232px;top:26px" width="14" height="18" viewBox="0 0 14 18" aria-hidden="true"><path d="M11 2 L4 9 L11 16" stroke="#e8f0de" stroke-width="2" fill="none"/></svg>
    <div class="month">MARCH</div>
    <svg class="abs" style="left:388px;top:26px" width="14" height="18" viewBox="0 0 14 18" aria-hidden="true"><path d="M3 2 L10 9 L3 16" stroke="#e8f0de" stroke-width="2" fill="none"/></svg>
    <div class="cell head" style="left:112px;top:68px">SUN</div>
    <div class="cell head" style="left:195px;top:68px">MON</div>
    <div class="cell head" style="left:273px;top:68px">TUE</div>
    <div class="cell head" style="left:347px;top:68px">WED</div>
    <div class="cell head" style="left:433px;top:68px">THR</div>
    <div class="cell head" style="left:509px;top:68px">FRI</div>
    <div class="cell head" style="left:581px;top:68px">SAT</div>

    <div class="cell" style="left:195px;top:112px">1</div><div class="cell" style="left:273px;top:112px">2</div><div class="cell" style="left:347px;top:112px">3</div><div class="cell" style="left:433px;top:112px">4</div><div class="cell" style="left:509px;top:112px">5</div><div class="cell" style="left:581px;top:112px">6</div>
    <div class="cell" style="left:112px;top:161px">7</div><div class="cell" style="left:195px;top:161px">8</div><div class="cell" style="left:273px;top:161px">9</div><div class="cell" style="left:347px;top:161px">10</div><div class="cell" style="left:433px;top:161px">11</div><div class="cell" style="left:509px;top:161px">12</div><div class="cell" style="left:581px;top:161px">13</div>
    <div class="cell" style="left:112px;top:216px">14</div><div class="cell" style="left:195px;top:216px">15</div><div class="cell" style="left:273px;top:216px">16</div><div class="cell" style="left:347px;top:216px">17</div><div class="cell" style="left:433px;top:216px">18</div><div class="cell" style="left:509px;top:216px">19</div><div class="cell" style="left:581px;top:216px">20</div>
    <div class="cell" style="left:112px;top:269px">21</div><div class="cell" style="left:195px;top:269px">22</div><div class="cell" style="left:273px;top:269px">23</div><div class="cell" style="left:347px;top:269px">24</div><div class="cell" style="left:433px;top:269px">25</div><div class="cell" style="left:509px;top:269px">26</div><div class="cell" style="left:581px;top:269px">27</div>
    <div class="cell" style="left:112px;top:321px">28</div><div class="cell" style="left:195px;top:321px">29</div><div class="cell" style="left:273px;top:321px">30</div><div class="cell" style="left:347px;top:321px">31</div>
  </div>
  <a class="abs btn" href="#" style="left:454px;top:2193px;width:290px;height:57px;line-height:57px;font-size:19px">Pay for Installation</a>

  <!-- about -->
  <h2 class="abs about-title" style="font-weight:400">ABOUT US</h2>
  <div class="abs" style="left:84px;top:2430px;font-family:'Cinzel',serif;font-size:14px;color:#444">PEBBLEBROOK PLOTS</div>
  <p class="abs body-copy" style="left:80px;top:2460px;width:636px">Lorem Ipsum is simply dummy text of the printing and typesetting industry. Lorem Ipsum has been the industry's standard dummy text ever since the 1500s, when an<br>Lorem Ipsum is simply dummy text of the printing and typesetting industry. Lorem Ipsum has been the industry's standard dummy text ever since the 1500s, when an unknown printer took a galley of type and scrambled it to make a type specimen book.</p>
  <a class="abs btn" href="#" style="left:78px;top:2613px;width:186px;height:56px;line-height:56px">Know More</a>
  <div class="abs video" role="img" aria-label="Video still of a gardener standing among her raised vegetable beds"></div>
  <div class="abs play"><svg width="80" height="58" viewBox="0 0 80 58" aria-hidden="true"><path d="M32 17 L52 29 L32 41Z" fill="#fff"/></svg></div>

  <!-- footer -->
  <div class="abs grass" role="img" aria-label="Band of grass blades growing from dark soil"></div>
  <footer class="abs footer"></footer>
  <div class="abs f-head" style="left:80px">UsefullLinks</div>
  <ul class="abs f-links"><li>Home</li><li>About</li><li>Order</li><li>Contact</li></ul>

  <div class="abs f-head" style="left:344px">Get In Touch</div>
  <svg class="abs" style="left:340px;top:2884px" width="16" height="22" viewBox="0 0 16 22" aria-hidden="true"><path d="M8 1 a7 7 0 0 1 7 7 c0 5 -7 13 -7 13 s-7 -8 -7 -13 a7 7 0 0 1 7 -7Z" fill="var(--green)"/><circle cx="8" cy="8" r="2.6" fill="var(--soil)"/></svg>
  <div class="abs f-text" style="left:370px;top:2882px;width:230px">PEBBLEBROOK PLOTS<br><span style="display:block;margin-left:0;color:#ddd">101 Lorem ipsum is simple dummy text of print and type setting industry</span></div>
  <svg class="abs" style="left:340px;top:3021px" width="18" height="18" viewBox="0 0 18 18" aria-hidden="true"><path d="M4 1 L7 5 L5 7 C6 10 8 12 11 13 L13 11 L17 14 L15 17 C8 17 1 10 1 3Z" fill="var(--green)"/></svg>
  <div class="abs f-text" style="left:372px;top:3019px">123 456 7890</div>
  <svg class="abs" style="left:340px;top:3063px" width="20" height="14" viewBox="0 0 20 14" aria-hidden="true"><rect width="20" height="14" rx="1" fill="var(--green)"/><path d="M1 1 L10 8 L19 1" stroke="var(--soil)" stroke-width="1.5" fill="none"/></svg>
  <div class="abs f-text" style="left:372px;top:3060px;font-size:13px">PebblebrookPlots@mailvale.com</div>

  <div class="abs f-head" style="left:617px">Community Feed</div>
  <div class="abs feed">
    <div class="abs" style="left:8px;top:10px;width:34px;height:34px;border:1px solid #ccc;background:#f1f1ea"></div>
    <div class="abs" style="left:50px;top:10px;font-family:'Cinzel',serif;font-size:11px;color:var(--orange)">PEBBLEBROOK PLOTS</div>
    <div class="abs" style="left:50px;top:30px;color:var(--green)">134 likes</div>
    <div class="abs" style="left:8px;top:58px">Share your thoughts below:</div>
    <div class="abs" style="left:8px;top:80px;width:238px;height:62px;background:linear-gradient(90deg,#8a9a78,#b7b9a5,#7c8c66)" role="img" aria-label="Thumbnail photos of finished raised garden beds"></div>
    <div class="abs" style="left:8px;top:172px;color:var(--green)">Embed</div>
    <div class="abs" style="left:140px;top:172px;color:var(--green)">View on Community Feed</div>
  </div>

  <div class="abs f-head" style="left:875px">Newsletter</div>
  <div class="abs field" style="top:2893px">Enter Name</div>
  <div class="abs field" style="top:2946px">Enter Email</div>
  <a class="abs btn" href="#" style="left:873px;top:2998px;width:145px;height:52px;line-height:52px;font-size:18px">Subscribe</a>

  <div class="abs center copyright">©<b>PEBBLEBROOK PLOTS</b>- 2016 All rights reserved.</div>
</div>
</body>
</html>
```